real esate business card with company logo and name

we need a business card design for a real esate company

The company name is Walsh & Brand Pty Ltd, and we have our logo designed and will upload. We want classic or moden feel. Black or white background. looks more textured. Should include folowinginformations
Owen Walsh and Lucy Brand
Sales Agents & Onsite Manager
p: 07 5948 2063
F: 07 5948 2174
M:0431 857 219
3/42 Marlow Crescent, FERNLEA QLD 4213

We want this business card looks professonal. Thank you in advance.

Industry/Entity Type

Real Estate Agent

Contact Information for Business Card

Owen Walsh and Lucy Brand
Onsite Manager & Sales Agents
p: 07 5948 2063
M:0431 857 219

Font styles to use
Serif

Colors
000000
fbfbfb
333333
959595

Requirements
Must have
• company logo and name, black or white back ground

```html
<!DOCTYPE html>
<html lang="en">
<head>
<meta charset="utf-8">
<title>Walsh &amp; Brand Pty Ltd — Business Card</title>
<link rel="stylesheet" href="https://fonts.googleapis.com/css2?family=Source+Sans+3:wght@400;600&family=Montserrat:wght@500&display=swap">
<style>
  :root {
    --page-bg: #eceef0;
    --card-top: #7e8185;
    --card-band: #2b2b2b;
    --card-bottom: #6c6e71;
    --ink-light: #fbfbfb;
    --icon-ink: #333333;
  }
  * { margin: 0; padding: 0; box-sizing: border-box; }
  html, body {
    width: 1200px;
    height: 1067px;
    overflow: hidden;
    background: var(--page-bg);
  }
  .card {
    position: absolute;
    left: 100px;
    top: 238px;
    width: 1000px;
    height: 590px;
    border-radius: 18px;
    overflow: hidden;
    background: var(--card-bottom);
    color: var(--ink-light);
    font-family: "Source Sans 3", sans-serif;
  }
  .card-shapes {
    position: absolute;
    inset: 0;
  }
  .brand {
    position: absolute;
    left: 0;
    right: 0;
    top: 200px;
    display: flex;
    align-items: center;
    justify-content: center;
    gap: 16px;
  }
  .brand-square {
    width: 30px;
    height: 30px;
    border: 4px solid var(--ink-light);
  }
  .brand-name {
    font-size: 48px;
    font-weight: 600;
    line-height: 1;
  }
  .company-line {
    position: absolute;
    left: 0;
    right: 0;
    top: 376px;
    text-align: center;
    font-family: "Montserrat", sans-serif;
    font-weight: 500;
    font-size: 19px;
    letter-spacing: 1px;
  }
  .people {
    position: absolute;
    left: 33px;
    top: 452px;
  }
  .people-names {
    font-size: 42px;
    font-weight: 400;
    line-height: 1.1;
  }
  .people-roles {
    font-size: 25px;
    line-height: 1.2;
    margin-top: 2px;
  }
  .contact {
    position: absolute;
    right: 36px;
    top: 438px;
    list-style: none;
    font-size: 24px;
    line-height: 34px;
    text-align: right;
  }
  .contact li {
    display: flex;
    justify-content: flex-end;
    align-items: center;
    gap: 18px;
  }
  .contact-icon {
    width: 21px;
    height: 21px;
    flex: none;
  }
  .contact-icon.blank { visibility: hidden; }
</style>
</head>
<body>
  <div class="card">
    <svg class="card-shapes" width="1000" height="590" viewBox="0 0 1000 590" aria-hidden="true">
      <rect width="1000" height="590" fill="var(--card-bottom)"/>
      <path d="M0 0 H1000 V33 Q500 183 0 33 Z" fill="var(--card-top)"/>
      <path d="M0 33 Q500 183 1000 33 V314 Q500 558 0 314 Z" fill="var(--card-band)"/>
    </svg>

    <div class="brand">
      <span class="brand-square"></span>
      <span class="brand-name">Walsh &amp; Brand</span>
    </div>
    <div class="company-line">WALSH &amp; BRAND PTY LTD.</div>

    <div class="people">
      <div class="people-names">Owen Walsh and Lucy Brand</div>
      <div class="people-roles">Onsite Manager &amp; Sales Agents</div>
    </div>

    <ul class="contact">
      <li>07 5948 2063
        <svg class="contact-icon" viewBox="0 0 21 21" aria-label="Phone">
          <rect width="21" height="21" fill="var(--ink-light)"/>
          <path d="M6 4 L8.5 4 L9.5 7.5 L8 8.8 Q9.5 12 12.2 13 L13.5 11.5 L17 12.5 L17 15 Q16 17 13.5 16.5 Q6.5 14.5 4.5 7.5 Q4.2 5 6 4 Z" fill="var(--icon-ink)"/>
        </svg>
      </li>
      <li>0431 857 219
        <svg class="contact-icon" viewBox="0 0 21 21" aria-label="Mobile">
          <rect width="21" height="21" fill="var(--ink-light)"/>
          <rect x="6" y="3" width="9" height="15" rx="1.5" fill="var(--icon-ink)"/>
          <rect x="7.5" y="5" width="6" height="6" fill="var(--ink-light)"/>
        </svg>
      </li>
      <li>3/42 Marlow Crescent,
        <svg class="contact-icon" viewBox="0 0 21 21" aria-label="Address">
          <rect width="21" height="21" fill="var(--ink-light)"/>
          <path d="M3.5 11 L10.5 4.5 L17.5 11 L15.5 11 L15.5 17 L12 17 L12 13 L9 13 L9 17 L5.5 17 L5.5 11 Z" fill="var(--icon-ink)"/>
        </svg>
      </li>
      <li>FERNLEA QLD 4213
        <span class="contact-icon blank"></span>
      </li>
    </ul>
  </div>
</body>
</html>
```